Modern Business Card for Larkwell 2018

Our company assumes the best about people. We are creating an online community of entrepreneurs and business leaders who struggle with marketing their business online.

This business card should POP! We recently got a new logo and are launching a new website next month, so our business cards should make a statement that feels:
-Fresh
-Smart
-Trustworthy
-Fun

Target Market(s)

small business owners, entrepreneurs

Industry/Entity Type

Digital Marketing

Contact Information for Business Card

Dimensions: 3.5" x 2"

Font styles to use
Sans Serif

Colors
f37122
ffffff

Requirements
Must have
• We need a business card with a modern, bold design. We will use one side of the card as a lead-generation offer, so text on one side will need to fit up to 140 characters. The business card should stick to our core colors (orange, black, and white).
Nice to have
• We think a vertical "portrait" design could be interesting.
Should not have
• Should not look like a traditional business card. The round icon should stand out from a distance.

```html
<!DOCTYPE html>
<html lang="en">
<head>
<meta charset="utf-8">
<title>Larkwell Business Card</title>
<link rel="stylesheet" href="https://fonts.googleapis.com/css2?family=Montserrat:wght@400;600;800&family=Roboto:wght@400;700&display=swap">
<style>
  :root {
    --orange: #f37122;
    --white: #ffffff;
    --ink: #1f1f1f;
    --grey: #6b6b6b;
    --stage: #e9e6e1;
    --rule: #8c8c8c;
  }
  * { box-sizing: border-box; margin: 0; padding: 0; }
  html, body { width: 1200px; height: 911px; overflow: hidden; }
  body {
    background: var(--stage);
    font-family: "Montserrat", sans-serif;
    position: relative;
  }
  .card {
    position: absolute;
    top: 158px;
    width: 340px;
    height: 595px;
    border-radius: 4px;
    overflow: hidden;
    box-shadow: 0 6px 18px rgba(0,0,0,0.18);
  }
  .card-front { left: 220px; background: var(--white); }
  .card-back { left: 640px; background: var(--orange); color: var(--white); }

  .wordmark {
    position: absolute; top: 62px; left: 0; right: 0;
    display: flex; justify-content: center; align-items: center; gap: 10px;
  }
  .wordmark-name {
    font-weight: 800; font-size: 36px; letter-spacing: 1px; color: var(--ink);
  }
  .wordmark-dot { width: 22px; height: 22px; border-radius: 50%; background: var(--orange); }
  .tagline {
    position: absolute; top: 112px; left: 0; right: 0; text-align: center;
    font-family: "Roboto", sans-serif; font-size: 11px; letter-spacing: 2px;
    text-transform: uppercase; color: var(--ink);
  }
  .person { position: absolute; top: 268px; left: 34px; }
  .person-name { font-weight: 600; font-size: 21px; color: var(--orange); text-transform: uppercase; }
  .person-role { font-size: 14px; color: var(--ink); text-transform: uppercase; margin-top: 4px; letter-spacing: 0.5px; }
  .email {
    position: absolute; bottom: 92px; left: 34px;
    font-family: "Roboto", sans-serif; font-size: 14px; letter-spacing: 3px; color: var(--grey);
  }

  .back-mark {
    position: absolute; top: 56px; left: 0; right: 0;
    display: flex; flex-direction: column; align-items: center; gap: 14px;
  }
  .back-circle { width: 150px; height: 150px; border-radius: 50%; background: var(--white); }
  .back-name { font-weight: 800; font-size: 22px; letter-spacing: 2px; color: var(--white); }
  .offer { position: absolute; top: 300px; left: 34px; right: 30px; }
  .offer-headline {
    font-weight: 800; font-size: 17px; line-height: 1.15; text-transform: uppercase;
  }
  .offer-body { font-family: "Roboto", sans-serif; font-size: 15px; line-height: 1.3; margin-top: 10px; }
  .offer-url { font-weight: 800; font-size: 17px; margin-top: 8px; }
  .notes {
    position: absolute; left: 22px; right: 22px; bottom: 34px; height: 104px;
    background: var(--white); border-radius: 12px; padding: 30px 18px 0;
  }
  .notes-line { height: 1px; background: var(--rule); margin-bottom: 30px; }
</style>
</head>
<body>
  <section class="card card-front" aria-label="Card front">
    <div class="wordmark">
      <span class="wordmark-name">LARKWELL</span>
      <span class="wordmark-dot"></span>
    </div>
    <p class="tagline">Tell stories that inspire action</p>
    <div class="person">
      <p class="person-name">Dana Whitfield</p>
      <p class="person-role">Story Marketing Coach</p>
    </div>
    <p class="email">dana@larkwellnow.com</p>
  </section>

  <section class="card card-back" aria-label="Card back">
    <div class="back-mark">
      <span class="back-circle"></span>
      <span class="back-name">LARKWELL</span>
    </div>
    <div class="offer">
      <p class="offer-headline">Reach more people.<br>Make more money.<br>Create more impact.</p>
      <p class="offer-body">Get your free Larkwell Starter Package and our marketing guide today at</p>
      <p class="offer-url">Larkwellnow.com/start</p>
    </div>
    <div class="notes">
      <div class="notes-line"></div>
      <div class="notes-line"></div>
    </div>
  </section>
</body>
</html>
```